Letter design, envelope design, and more

Hello, we the Tavrin Gmbh are looking for our shop. Letter C5. Design does not have to be like a business card, so it can have straight lines. Only the color is important. The logo is the text under TaVRin omit.It should not be playful but Profesionel

Font styles to use
Sans Serif

Colors
0555a3
3176b5
85abd2
85cae6
34a7d8
0792cd
cee9f5
cfdfed
000000

Requirements
Must have
• Color like business card, Please, with the text under TaVRin, Correct address Lindmattstr. 4 Zip code 9517 Goldach, as well as Couvert Without addressing only design and logo with TaVrn
Nice to have
• more writing articles
Should not have
• Not too colored, Text under TaVRin, bright colors

```html
<!DOCTYPE html>
<html lang="en">
<head>
<meta charset="utf-8">
<title>TaVRin Gmbh – Stationery</title>
<link rel="stylesheet" href="https://fonts.googleapis.com/css2?family=Jost:wght@400&family=Montserrat:wght@700&family=Roboto:wght@400&display=swap">
<style>
  :root {
    --backdrop: #dcdcdc;
    --paper: #f7f7f7;
    --navy: #0a1f5c;
    --steel: #8a909c;
    --ink: #3d3d3d;
    --ink-soft: #555a60;
    --signature-tone: #dfe6f2;
  }
  * { margin: 0; padding: 0; box-sizing: border-box; }
  html, body { width: 1200px; height: 877px; overflow: hidden; }
  body { background: var(--backdrop); position: relative; font-family: "Roboto", sans-serif; }

  .brand { display: flex; align-items: center; gap: 7px; }
  .brand-square { width: 22px; height: 22px; background: var(--navy); }
  .brand-name { font-family: "Montserrat", sans-serif; font-weight: 700; color: var(--navy); font-size: 24px; letter-spacing: 1px; line-height: 1; }

  .edge-bar { position: absolute; left: 0; top: 0; bottom: 0; width: 8px; background: var(--navy); }
  .edge-bar::before { content: ""; position: absolute; left: 0; top: 0; width: 100%; height: var(--steel-height); background: var(--steel); }

  /* Letterhead */
  .letterhead { position: absolute; left: 68px; top: 63px; width: 528px; height: 743px; background: var(--paper); }
  .letterhead .edge-bar { --steel-height: 158px; }
  .letterhead .brand { position: absolute; left: 48px; top: 43px; }
  .letter-contact { position: absolute; left: 403px; top: 42px; border-left: 1px solid #c9ccd2; padding-left: 8px; font-size: 7.6px; line-height: 9.6px; color: var(--ink); }
  .letter-contact .street { margin-bottom: 5px; }
  .contact-line { display: flex; align-items: center; gap: 4px; }
  .contact-line svg { width: 7px; height: 7px; fill: var(--navy); }
  .salutation { position: absolute; left: 46px; top: 208px; font-family: "Jost", sans-serif; font-size: 13.6px; color: var(--ink-soft); }
  .letter-body { position: absolute; left: 46px; top: 247px; width: 438px; font-family: "Jost", sans-serif; font-size: 7.5px; line-height: 11.4px; color: var(--ink); text-align: justify; }
  .letter-body p { margin-bottom: 11.4px; }
  .closing { position: absolute; left: 46px; top: 487px; font-family: "Jost", sans-serif; font-size: 7.6px; color: var(--ink); }
  .signature { position: absolute; left: 42px; top: 518px; width: 94px; height: 42px; background: var(--signature-tone); border-radius: 4px; }
  .letter-footer { position: absolute; left: 0; right: 0; top: 723px; text-align: center; font-size: 8px; letter-spacing: 1px; color: var(--ink); }

  /* Envelope back */
  .envelope-back { position: absolute; left: 614px; top: 269px; width: 531px; height: 241px; background: var(--paper); }
  .envelope-flap { position: absolute; left: 0; top: 0; width: 531px; height: 74px; }
  .flap-name { position: absolute; left: 0; right: 0; top: 26px; text-align: center; font-family: "Montserrat", sans-serif; font-weight: 700; color: var(--paper); font-size: 22px; letter-spacing: 1px; }

  /* Envelope front */
  .envelope-front { position: absolute; left: 613px; top: 562px; width: 533px; height: 241px; background: var(--paper); }
  .envelope-front .edge-bar { width: 10px; --steel-height: 82px; }
  .envelope-front .brand { position: absolute; left: 35px; top: 28px; }
  .sender-line { position: absolute; left: 35px; top: 67px; font-size: 7.6px; color: var(--ink); }
</style>
</head>
<body>

<section class="letterhead">
  <div class="edge-bar"></div>
  <div class="brand"><span class="brand-square"></span><span class="brand-name">TaVRin</span></div>
  <address class="letter-contact" style="font-style:normal">
    <div class="street">Lindmattstr. 4<br>9517 Goldach</div>
    <div class="contact-line"><svg viewBox="0 0 10 10"><path d="M2 0.5 L4 2.8 L3 4 C3.6 5.3 4.7 6.4 6 7 L7.2 6 L9.5 8 L8 9.6 C4 9 1 6 0.4 2 Z"/></svg>+41 71 420 36 18</div>
    <div class="contact-line"><svg viewBox="0 0 10 10"><path d="M0 2 H10 V8.5 H0 Z M0.8 2.6 L5 5.6 L9.2 2.6" stroke="#f7f7f7" stroke-width="0.8"/></svg>info@tavrin.ch</div>
  </address>

  <p class="salutation">Dear Mr. Keller,</p>
  <div class="letter-body">
    <p>Lorem ipsum dolor sit amet, consectetur adipiscing elit. Donec orci purus, luctus vitae dignissim eu, iaculis sed purus. Vivamus faucibus, ipsum nec aliquet viverra, leo mauris condimentum ligula, sit amet sagittis enim ligula quis arcu. Nam egestas tortor id nisi porttitor mattis. In tortor ante, ultricies in suscipit a, tempus non massa. Vivamus et auctor mi. Fusce vel massa nulla. Phasellus nec eros mauris, et scelerisque orci.</p>
    <p>Donec malesuada orci vitae nulla accumsan porta a id massa. Quisque accumsan iaculis magna sit amet fringilla. Maecenas consequat, magna eget tincidunt semper, odio nibh rutrum mi, id feugiat ante nisi eu risus. Vestibulum nunc orci, rhoncus a placerat in, ultricies in mi. Cras mattis varius eros, vel fringilla nisi suscipit eget. Quisque scelerisque sagittis nulla at porttitor.</p>
    <p>Sed id augue vitae urna euismod commodo aliquet a quam. Pellentesque arcu velit, cursus et malesuada ut, consequat et diam. Nullam erat sem, rhoncus id ullamcorper vitae, rhoncus et arcu. In ultricies ultricies nulla, ut rutrum nisi iaculis at. Donec eu magna a metus ornare faucibus. Fusce aliquet faucibus ultricies. Morbi semper, est id tincidunt gravida, sem arcu adipiscing lacus, ac bibendum nulla leo eu purus. Quisque nec diam sed risus consectetur a ccumsan quis quis nibh. Vestibulum id purus lorem.</p>
    <p>It is a long established fact that a reader will be distracted by the readable content of a page when looking at its layout. The point of using Lorem Ipsum is that it has a more-or-less normal distribution of letters, as opposed to using 'Content here, content here', making it look like readable English. Many desktop publishing packages</p>
  </div>
  <p class="closing">Sincerely,</p>
  <div class="signature" role="img" aria-label="Handwritten signature of Jonas Keller"></div>
  <p class="letter-footer">www.tavrin.ch</p>
</section>

<section class="envelope-back">
  <svg class="envelope-flap" viewBox="0 0 531 74" aria-hidden="true">
    <path d="M0 0 H531 L522 48 C519 64 508 74 492 74 H39 C23 74 12 64 9 48 Z" fill="var(--navy)"/>
  </svg>
  <div class="flap-name">TaVrn</div>
</section>

<section class="envelope-front">
  <div class="edge-bar"></div>
  <div class="brand"><span class="brand-square"></span><span class="brand-name">TaVRin</span></div>
  <p class="sender-line">Lindmattstr. 4, 9517 Goldach</p>
</section>

</body>
</html>
```